Business card por a urban DJ, up scale audience target

Need a sober design, modern, conservative colors but i can consider some options, y play rnb, hip hop, EDM and top40.

Business card for contact and personal info, double sided, use logo attrached please; im 42 so i need a card acording to my age an target audience.

Target Market(s)

Adult people, up scale audience

Industry/Entity Type

Music Download

Contact Information for Business Card

Cel (318) 4207265518 www.lumadrift.com

Requirements
Must have
• open mind
Nice to have
• open mind
Should not have
• DJ

```html
<!DOCTYPE html>
<html lang="en">
<head>
<meta charset="utf-8">
<title>LUMA business card</title>
<link rel="stylesheet" href="https://fonts.googleapis.com/css2?family=Open+Sans:wght@400;600;800&display=swap">
<style>
  :root {
    --backdrop: #cfcfcf;
    --card: #262626;
    --card-edge: #1a1a1a;
    --ink: #ffffff;
    --ink-soft: #d9d9d9;
    --rule: #bdbdbd;
  }
  * { box-sizing: border-box; margin: 0; padding: 0; }
  html, body { width: 1200px; height: 800px; overflow: hidden; }
  body {
    background: var(--backdrop);
    font-family: "Open Sans", sans-serif;
    color: var(--ink);
    display: flex;
    align-items: center;
    justify-content: center;
    gap: 120px;
  }
  .card {
    width: 300px;
    height: 525px;
    background: linear-gradient(160deg, #333 0%, var(--card) 45%, var(--card-edge) 100%);
    border-radius: 4px;
    box-shadow: 0 12px 30px rgba(0,0,0,.35);
    position: relative;
  }
  .card-front { display: flex; align-items: center; justify-content: center; }
  .brand-name {
    font-weight: 800;
    letter-spacing: 2px;
    line-height: 1;
    color: var(--ink);
  }
  .card-front .brand-name {
    font-size: 92px;
    transform: rotate(-90deg);
  }
  .card-back .brand-name {
    font-size: 84px;
    position: absolute;
    top: 42px;
    left: 0; right: 0;
    text-align: center;
  }
  .contact-frame {
    position: absolute;
    left: 22px; right: 22px;
    top: 192px; bottom: 60px;
    border: 1.5px solid var(--rule);
    border-radius: 28px;
    text-align: center;
  }
  .holder {
    position: absolute;
    top: -12px;
    left: 50%;
    transform: translateX(-50%);
    background: var(--card);
    padding: 0 12px;
    white-space: nowrap;
  }
  .holder-name { font-size: 16px; letter-spacing: .5px; color: var(--ink-soft); line-height: 1.1; }
  .holder-role { font-size: 10px; color: var(--ink-soft); }
  .contact-list { list-style: none; padding: 42px 18px 0; }
  .contact-item { padding-bottom: 8px; }
  .contact-item + .contact-item { border-top: 1px solid var(--rule); padding-top: 10px; }
  .contact-item svg { display: block; margin: 0 auto 4px; }
  .contact-value { font-size: 18px; letter-spacing: .4px; color: var(--ink); }
</style>
</head>
<body>
  <section class="card card-front" aria-label="Card front">
    <span class="brand-name">LUMA</span>
  </section>

  <section class="card card-back" aria-label="Card back">
    <span class="brand-name">LUMA</span>
    <div class="contact-frame">
      <div class="holder">
        <div class="holder-name">JONATHAN DOE</div>
        <div class="holder-role">Managing Director</div>
      </div>
      <ul class="contact-list">
        <li class="contact-item">
          <svg width="14" height="12" viewBox="0 0 14 12" aria-hidden="true"><path d="M1 4 Q7 -1 13 4 L11 5 L9.5 3.5 L4.5 3.5 L3 5 Z M3 6 H11 L12 11 H2 Z" fill="#ddd"/></svg>
          <span class="contact-value">(318) 4207265518</span>
        </li>
        <li class="contact-item">
          <svg width="16" height="12" viewBox="0 0 16 12" aria-hidden="true"><rect x="1" y="1" width="14" height="10" fill="none" stroke="#ddd" stroke-width="1.3"/><path d="M1 1 L8 7 L15 1" fill="none" stroke="#ddd" stroke-width="1.3"/></svg>
          <span class="contact-value">info@yourwebsite.com</span>
        </li>
        <li class="contact-item">
          <svg width="16" height="14" viewBox="0 0 16 14" aria-hidden="true"><rect x="1" y="1" width="14" height="9" fill="none" stroke="#ddd" stroke-width="1.3"/><path d="M6 13 H10 M8 10 V13" stroke="#ddd" stroke-width="1.3"/></svg>
          <span class="contact-value">www.lumadrift.com</span>
        </li>
      </ul>
    </div>
  </section>
</body>
</html>
```